Accountability Project Graphics

I want to create 10 social media graphics (new Instagram size 4:5 (1080 x 1350 pixels) focusing on our Quilvo Accountability App, using any of the 3 pictures attached. Use the attached pics only, NO RANDOM STOCK PHOTOGRAPHY. For the color scheme, use the landing page colors/fonts (attached).
You can add any of the 3 photos attached but I mainly need BOLD text that includes these headlines and sub-headlines on them.
Please NOTE for all the headlines below, also add this sub-headline on each graphic:
Stay Consistent with RT in Your Pocket!
Here are the headlines:
• Stop Starting Over Every Monday
• You don't need more willpower. You need more support
• Built for women who are tired of doing this alone
• When Motivation Fades, RT Checks In
• The Support System You've Been Missing
• Support When Motivation Disappears
• What if RT Checked in Every Day?
• The Missing Piece Isn't Another Diet
• Eat the food you love. Stay accountable every day.
• One Bad Meal Doesn't Mean You Failed
women over 40 trying to lose weight

```html
<!DOCTYPE html>
<html lang="en">
<head>
<meta charset="UTF-8">
<title>Eat the Food You Love – Quilvo Accountability</title>
<link href="https://fonts.googleapis.com/css2?family=Bebas+Neue&family=Montserrat:wght@600&display=swap" rel="stylesheet">
<style>
  :root {
    --bg-slate: #a9bbc9;
    --pink: #d84f7c;
    --plum: #2f1a3e;
    --bar-plum: #331b3d;
    --white: #ffffff;
    --photo-top: #8a7a68;
    --photo-mid: #4b3f3e;
    --photo-low: #3a3034;
    --photo-floor: #cfd4d8;
  }
  html, body {
    margin: 0;
    padding: 0;
    overflow: hidden;
  }
  .canvas {
    position: relative;
    width: 960px;
    height: 1200px;
    background: var(--bg-slate);
    overflow: hidden;
    font-family: "Bebas Neue", "Oswald", sans-serif;
  }
  .hero-photo {
    position: absolute;
    left: 380px;
    top: 0;
    width: 580px;
    height: 1111px;
    background: linear-gradient(180deg, var(--photo-top) 0%, var(--photo-mid) 45%, var(--photo-low) 80%, var(--photo-floor) 100%);
    -webkit-mask-image: linear-gradient(90deg, transparent 0%, #000 30%);
    mask-image: linear-gradient(90deg, transparent 0%, #000 30%);
  }
  .headline {
    position: absolute;
    left: 80px;
    margin: 0;
    font-size: 149px;
    font-weight: 400;
    line-height: 1;
    letter-spacing: -2px;
    -webkit-text-stroke: 4px var(--white);
    paint-order: stroke fill;
  }
  .headline-pink { color: var(--pink); top: 128px; }
  .headline-plum { color: var(--plum); }
  .line-food { top: 272px; }
  .line-love { top: 415px; }
  .pill {
    position: absolute;
    left: 0;
    height: 107px;
    background: var(--pink);
    border-radius: 0 54px 54px 0;
    color: var(--white);
    font-size: 95px;
    line-height: 114px;
    letter-spacing: -2px;
    padding-left: 76px;
    box-sizing: border-box;
  }
  .pill-stay { top: 600px; width: 286px; }
  .pill-accountable { top: 730px; width: 526px; }
  .pill-every-day { top: 860px; width: 437px; }
  .footer-bar {
    position: absolute;
    left: 0;
    top: 1111px;
    width: 960px;
    height: 89px;
    background: var(--bar-plum);
  }
  .footer-tagline {
    position: absolute;
    left: 0;
    width: 960px;
    top: 1141px;
    text-align: center;
    font-family: "Montserrat", "Arial", sans-serif;
    font-weight: 600;
    font-size: 28px;
    line-height: 1;
    color: var(--white);
  }
  .app-badge {
    position: absolute;
    left: 56px;
    top: 1066px;
    width: 88px;
    height: 88px;
  }
  .ref-code {
    position: absolute;
    right: 36px;
    top: 1166px;
    font-family: "Montserrat", "Arial", sans-serif;
    font-size: 13px;
    color: var(--white);
  }
</style>
</head>
<body>
<div class="canvas">
  <div class="hero-photo" role="img" aria-label="Photo of the smiling coach in a black lace top and black jeans, hand on hip, leaning on a pool table in a lounge"></div>

  <h1 class="headline headline-pink">EAT THE</h1>
  <div class="headline headline-plum line-food">FOOD</div>
  <div class="headline headline-plum line-love">YOU LOVE.</div>

  <div class="pill pill-stay">STAY</div>
  <div class="pill pill-accountable">ACCOUNTABLE</div>
  <div class="pill pill-every-day">EVERY DAY.</div>

  <div class="footer-bar"></div>
  <svg class="app-badge" viewBox="0 0 88 88" aria-hidden="true">
    <circle cx="44" cy="44" r="44" fill="#d84f7c"/>
    <g fill="none" stroke="#ffffff" stroke-width="2.2" stroke-linecap="round" stroke-linejoin="round">
      <rect x="22" y="24" width="34" height="26" rx="3"/>
      <line x1="30" y1="58" x2="42" y2="58"/>
      <line x1="36" y1="50" x2="36" y2="58"/>
      <circle cx="32" cy="34" r="5"/>
      <rect x="46" y="34" width="20" height="32" rx="3" fill="#d84f7c"/>
      <circle cx="56" cy="50" r="6"/>
      <polyline points="53,50 55.5,52.5 59.5,47.5"/>
    </g>
  </svg>
  <div class="footer-tagline">STAY CONSISTENT WITH RT IN YOUR POCKET!</div>
  <div class="ref-code">C58</div>
</div>
</body>
</html>
```